Covid 19 Exit Strategy one page brochure

I would like to design, and will need URGENT help, a brochure detailing a Covid 19 Exit Strategy plan. This brochure will need to be understood easily and the graphics inside should make it easy for people to understand without reading the entire text. This project is quite urgent and needs to be completed THIS WEEK - by Saturday may 16th at the latest. I am attaching two examples. I will provide the text.

```html
<!DOCTYPE html>
<html lang="en">
<head>
<meta charset="utf-8">
<title>COVID-19 Phased Exit Strategy</title>
<link rel="stylesheet" href="https://fonts.googleapis.com/css2?family=Montserrat:wght@600;700;800&family=Open+Sans:wght@400;600;700&display=swap">
<style>
:root{
  --page:#e4e4e4;
  --red:#e52421;
  --blue:#3fa0dc;
  --navy:#0f2f63;
  --navy-2:#1d5aa3;
  --ink:#2f3b4a;
  --line:#d4d8dd;
  --icon:#d8e8f6;
  --icon-alt:#f6d9d8;
  --white:#ffffff;
}
*{box-sizing:border-box;margin:0;padding:0}
html,body{width:1200px;height:4000px;overflow:hidden;background:var(--page)}
body{font-family:"Open Sans",Arial,sans-serif;color:var(--ink)}
.poster{position:absolute;left:287px;top:101px;width:626px;height:3798px;overflow:hidden;background:var(--blue)}

.masthead{height:179px;position:relative;text-align:center;color:var(--white);
  background:radial-gradient(circle at 12% 30%,#3b78c4 0,transparent 28%),radial-gradient(circle at 88% 70%,#3b78c4 0,transparent 28%),linear-gradient(180deg,var(--navy),var(--navy-2))}
.masthead h1{font-family:"Montserrat",Arial,sans-serif;font-weight:800;font-size:34px;line-height:1;padding-top:34px}
.masthead .accent{display:block;color:var(--red);font-size:33px;margin-top:8px}
.masthead p{font-family:"Montserrat",Arial,sans-serif;font-weight:600;font-size:24px;margin-top:8px}

.intro{height:404px;background:var(--red);color:var(--white);padding:18px 31px 0}
.intro .lead{font-size:8.6px;line-height:1.45;font-weight:600}
.section-label{display:block;width:240px;margin:16px auto 18px;background:var(--white);color:var(--red);
  font-family:"Montserrat",Arial,sans-serif;font-weight:800;font-size:16px;text-align:center;padding:5px 0}
.requirements{display:grid;grid-template-columns:1fr 1fr;column-gap:28px;list-style:none}
.requirements li{display:flex;gap:7px;font-size:8.6px;line-height:1.4;font-weight:600;margin-bottom:10px}
.requirements .num{flex:none;width:15px;height:15px;border-radius:50%;background:var(--white);color:var(--red);
  font-weight:700;font-size:9px;text-align:center;line-height:15px}

.stage{position:relative;padding:0 31px}
.stage--blue{background:var(--blue)}
.stage--red{background:var(--red)}
.stage-1{height:1115px}
.stage-2{height:1098px}
.stage-3{height:927px}
.plan-title{background:var(--white);color:#111;font-family:"Montserrat",Arial,sans-serif;font-weight:800;font-size:19px;
  text-align:center;padding:8px 0;margin:5px 0 10px}
.stage-tag{display:block;width:158px;margin:0 auto;background:var(--white);font-family:"Montserrat",Arial,sans-serif;
  font-weight:800;font-size:28px;text-align:center;line-height:38px}
.stage-tag--spaced{margin-top:12px}
.stage--blue .stage-tag{color:var(--blue)}
.stage--red .stage-tag{color:var(--red)}
.stage-note{color:var(--white);font-size:8.4px;line-height:1.4;margin-top:14px}
.stage-sub{color:var(--white);font-size:10.5px;font-weight:600;margin:6px 0 10px}

.grid{display:grid;grid-template-columns:repeat(3,1fr);background:var(--white);border:2px solid var(--white)}
.stage-1 .grid{grid-template-rows:124px 160px 189px 199px 264px}
.stage-2 .grid{grid-template-rows:134px 140px 174px 189px 168px 140px}
.stage-3 .grid{grid-template-rows:155px 140px 151px 160px 179px}
.cell{border:1px solid var(--line);padding:12px 9px 4px;text-align:center;font-size:8.7px;line-height:1.28;color:#3a4452;overflow:hidden}
.cell--wide{grid-column:span 3;padding-left:40px;padding-right:40px}
.cell--span2{grid-column:span 2;padding-left:20px;padding-right:20px}
.icon{display:block;width:42px;height:42px;margin:0 auto 10px;border-radius:8px;background:var(--icon)}
.icon--alt{background:var(--icon-alt)}

.footer{height:75px;background:var(--blue);padding-top:12px}
.footer-bar{display:flex;align-items:center;height:42px;background:var(--red);color:var(--white)}
.footer-brand{display:flex;align-items:center;gap:8px;height:100%;width:205px;background:var(--white);padding-left:14px;
  color:var(--red);font-size:10px;font-weight:700}
.footer-brand .mark{width:18px;height:18px;background:var(--red)}
.footer-tag{flex:1;padding-left:20px;font-size:9px;line-height:1.35}
.footer-tag b,.footer-info b{font-weight:700}
.footer-info{width:200px;font-size:9px;line-height:1.35}
</style>
</head>
<body>
<main class="poster">

  <header class="masthead" role="img" aria-label="Dark blue banner with magnified virus particles behind the title">
    <h1>COVID-19<span class="accent">PHASED EXIT STRATEGY</span></h1>
    <p>Developed by Lena Morvan</p>
  </header>

  <section class="intro">
    <p class="lead">Pandemics have, historically, seen their end both medically - via herd immunity or immunizations. And while there are several clinical trials underway for potential Covid-19 vaccines, we are still a long way from deploying an effective vaccine and one that will stand the test of time as the virus changes. Covid-19 pandemic will be considered 'ended' when there are only occasional traces of localized cases that are quickly contained in specific locations. Today and in the absence of an effective vaccine(s) and for the re-opening of the economies and social activities to be successful, it is critical that the following basic conditions be in place before any lockdowns are lifted and before social activities resume:</p>
    <h2 class="section-label">GENERAL REQUIREMENTS:</h2>
    <ol class="requirements">
      <li><span class="num">1</span>Single digit downward trend of documented cases within the past 14- days.</li>
      <li><span class="num">6</span>Plan in place to trigger targeted or full-scale containment in case of sudden outbreaks.</li>
      <li><span class="num">2</span>Hospitals and the health care system are capable of treating patients without operating on a crisis mode.</li>
      <li><span class="num">7</span>Mandatory use of masks (at least surgical grade) for everyone in all public areas and at work. Mandatory use of N95, or equivalent, masks for all healthcare front workers and for all government agencies and authorities that are involved in overseeing the containment activities.</li>
      <li><span class="num">3</span>Ability to screen and test symptomatic individuals within 24 hours of identification. Increased and sufficient testing capacity, to test at least 50% of all population if necessary within a timeframe of 3 months.</li>
      <li><span class="num">8</span>Mandatory daily checks of body temperature for everyone at the workplace or entering public areas.</li>
      <li><span class="num">4</span>Ability to surge ICU capacity on a short notice - 24h.</li>
      <li><span class="num">9</span>Mandatory sanitation in all places - use of disinfection available on a large scale.</li>
      <li><span class="num">5</span>Ability to track and trace infected patients and contacts on a live basis and across the country and ability to react quickly to any unusual trends or</li>
    </ol>
  </section>

  <section class="stage stage--blue stage-1">
    <h2 class="plan-title">PHASED COVID-19 LOCKDOWN EXIT STRATEGY PLAN</h2>
    <h3 class="stage-tag">STAGE : 1</h3>
    <p class="stage-note">To enter this stage, additional to the general requirements, the Effective Reproduction Number (Rt) must be less than 1 and the death rate at less than 3%.</p>
    <p class="stage-sub">The economy and social activities can resume in this sequence:</p>
    <div class="grid">
      <div class="cell"><span class="icon" role="img" aria-label="Elderly person icon"></span>Elderly (60+ years old) and vulnerable individuals should continue to self-isolate.</div>
      <div class="cell"><span class="icon icon--alt" role="img" aria-label="No gathering icon"></span>No more than 5 people maximum gathering at a time in public areas and at work.</div>
      <div class="cell"><span class="icon" role="img" aria-label="Work from home icon"></span>Work from home should continue whenever and as much as possible.</div>
      <div class="cell"><span class="icon" role="img" aria-label="Social distancing icon"></span>Social distancing should continue to be re-enforced in public areas, at work and in all areas reopened.</div>
      <div class="cell"><span class="icon icon--alt" role="img" aria-label="No travel icon"></span>Non-essential travel should be minimized between cities and regions (and within cities and regions where covid-19 infections are still a risk)</div>
      <div class="cell"><span class="icon" role="img" aria-label="Factory icon"></span>Large businesses (300 people and more, manufacturing, services, etc.) can reopen progressively. Common areas should remain closed (cafeteria, restaurant, gym, meeting rooms of no more than 5 people).</div>
      <div class="cell"><span class="icon" role="img" aria-label="Small shop icon"></span>Small businesses (300 people and less) can reopen as well with the same conditions as large businesses.</div>
      <div class="cell"><span class="icon" role="img" aria-label="Store icon"></span>Commercial shops can reopen. Shops should control the flow of people in their facilities not to exceed 30% at a time of standard capacity. Shops should provide disinfectant and temperature control at entry.</div>
      <div class="cell"><span class="icon" role="img" aria-label="Pharmacy icon"></span>Pharmacies will continue to be open. However, they must make available disinfectant for use by clients and will continue to comply with social distancing. Pharmacies should limit the number of client/patient in their stores not to exceed 30% of the standard capacity.</div>
      <div class="cell"><span class="icon" role="img" aria-label="Religious building icon"></span>Religious sites can reopen with a maximum capacity of 30% or less. Social distancing and wearing masks is mandatory. Religious sites should organize (volunteers can help) to check body temperature of everyone accessing the site and provide disinfectant at entry.</div>
      <div class="cell"><span class="icon" role="img" aria-label="Hotel icon"></span>Hotels &amp; tourism (museums, etc.) can reopen but must operate at 30% or less capacity. All common areas (restaurants, gyms, swimming pools, conference rooms, etc.) should remain closed.</div>
      <div class="cell"><span class="icon icon--alt" role="img" aria-label="Closed school icon"></span>All schools should remain closed. On-line courses should continue be the preferred method for education.</div>
      <div class="cell"><span class="icon" role="img" aria-label="Delivery truck icon"></span>Transportation (buses, taxis, airlines) will resume progressively. No air travels permitted in and out of Covid-19 known hotspots, locally or internationally. Entry to country should be limited and strictly controlled. All landing passengers and visitors regardless of the country of origin should be tested for Covid-19 at arrival. All passengers and visitors will undergo a temperature check at arrival. No more than 3 people at a time in a taxi/RideLink including the driver. All passengers wearing masks. Buses should operate with no more than 30% customer's capacity per bus.</div>
      <div class="cell"><span class="icon" role="img" aria-label="Cafe icon"></span>Coffee &amp; restaurants can reopen but must operate at 30% capacity as well and comply with social distancing. Clients must wear as much as possible their masks if they are not consuming food/coffee. Clients should avoid to talking to each other with masks off.</div>
      <div class="cell"><span class="icon icon--alt" role="img" aria-label="Closed venue icon"></span>Large scale events (cinema, theaters, sport, business conferences, etc.) should remain closed or operate virtually. Sport events can resume but without spectators. Athletes and the staff surrounding them should be tested, disinfectants should be available and masks used as much as reasonably possible.</div>
    </div>
  </section>

  <section class="stage stage--red stage-2">
    <h3 class="stage-tag stage-tag--spaced">STAGE : 2</h3>
    <p class="stage-note">To enter stage 2 of the Covid-19 Exit Strategy, compliance to the general requirements is compulsory, additional to a successful Stage 1 outcome. The Effective Reproduction Number (Rt) for Stage 2 must be less than 0.5 and the death rate stabilized at less than 1.5%.</p>
    <p class="stage-sub">The economy and social activities can resume in this sequence:</p>
    <div class="grid">
      <div class="cell"><span class="icon" role="img" aria-label="Elderly person icon"></span>Elderly (60+ years old) and vulnerable individuals should continue to self-isolate as much as possible.</div>
      <div class="cell"><span class="icon icon--alt" role="img" aria-label="No gathering icon"></span>No more than 10 people maximum gathering at a time in public areas and at work.</div>
      <div class="cell"><span class="icon" role="img" aria-label="Work from home icon"></span>Work from home should if possible or for jobs that do not have to be necessarily in an office setup.</div>
      <div class="cell"><span class="icon" role="img" aria-label="Social distancing icon"></span>Social distancing can be relaxed. However people should continue to wear masks and use disinfectants.</div>
      <div class="cell"><span class="icon icon--alt" role="img" aria-label="Travel icon"></span>Travel can resume between cities and regions. The same containment restrictions should apply to any existing hotspot.</div>
      <div class="cell"><span class="icon" role="img" aria-label="Hospital icon"></span>Elective surgeries can resume in hospitals and clinics that are equipped to comply with all general requirements.</div>
      <div class="cell"><span class="icon" role="img" aria-label="Factory icon"></span>Large businesses (300 people and more, manufacturing, services, etc.) will continue to operate. Common areas should open but social distancing should remain (cafeteria, restaurant, gym, meeting rooms of no more than 10 people).</div>
      <div class="cell"><span class="icon" role="img" aria-label="Small shop icon"></span>Small businesses (300 people and less) will continue to operate with the same conditions as large businesses.</div>
      <div class="cell"><span class="icon" role="img" aria-label="Store icon"></span>Commercial shops will continue to be open and can operate at 50% capacity. Wear of masks should continue.</div>
      <div class="cell"><span class="icon" role="img" aria-label="Pharmacy icon"></span>Commercial shops will continue to be open and can operate at 50% capacity. Wear of masks should continue.</div>
      <div class="cell"><span class="icon" role="img" aria-label="Religious building icon"></span>Religious sites can operate with a maximum capacity of 50%. Social distancing and wearing masks should be enforced. Sites should continue to check body temperature of everyone accessing the site and provide disinfectant at entry.</div>
      <div class="cell"><span class="icon" role="img" aria-label="Hotel icon"></span>Hotels &amp; tourism (museums, etc.) can operate at 50% capacity. All common areas (restaurants, gyms, swimming pools, conference rooms, etc.) could reopen. Gatherings are limited to 10 people or less and can be expanded with social distancing and wearing protective masks.</div>
      <div class="cell"><span class="icon" role="img" aria-label="Cafe icon"></span>Coffee &amp; restaurants can operate at 50% capacity and continue comply with social distancing. Clients must wear as much as possible their masks if they are not consuming food/coffee.</div>
      <div class="cell"><span class="icon icon--alt" role="img" aria-label="School icon"></span>Schools can reopen in parallel with on-line education. Social distancing and re-arranging school seating to prevent the spread of infection is mandatory.</div>
      <div class="cell"><span class="icon icon--alt" role="img" aria-label="Venue icon"></span>Large scale events (cinema, theaters, sport, business conferences, etc.) could resume under strict social distancing. People should wear masks.</div>
      <div class="cell cell--wide"><span class="icon" role="img" aria-label="Delivery truck icon"></span>Transportation (buses, taxis, and airlines) will continue to operate. Still no air travels permitted in and out of Covid-19 known hotspots, locally or internationally. Entry to country should be relaxed but remain controlled. Airports should continue to use thermo cameras to monitor passenger's temperature at landing. Airports should be equipped to test for Covid-19 if necessary. Transportation by taxi/RideLink continues, however, passengers wear masks. Buses could operate with 50% capacity per bus.</div>
    </div>
  </section>

  <section class="stage stage--blue stage-3">
    <h3 class="stage-tag stage-tag--spaced">STAGE : 3</h3>
    <p class="stage-note">To enter stage 3 of the Covid-19 Exit Strategy, compliance to the general requirements is compulsory, additional to a successful Stage 2 outcome. The Effective Reproduction Number (Rt) for Stage 3 must be less than 0.3 and the death rate stabilized at less than 1%.</p>
    <p class="stage-sub">The economy and social activities can resume in this sequence:</p>
    <div class="grid">
      <div class="cell"><span class="icon" role="img" aria-label="Elderly person icon"></span>Elderly (60+ years old) and vulnerable individuals may resume all previously exercised activities without restrictions.</div>
      <div class="cell"><span class="icon icon--alt" role="img" aria-label="Gathering icon"></span>Restrictions as to the number of people gathering together can be lifted. Social distancing can be relaxed. However, wear of masks may continue.</div>
      <div class="cell"><span class="icon" role="img" aria-label="Luggage and plane icon"></span>Travel can resume between cities and regions and out of country travel. The same containment restrictions as Stage 1 and 2 would continue to apply to any existing hotspot.</div>
      <div class="cell"><span class="icon" role="img" aria-label="Hospital icon"></span>All hospital and clinic surgeries can resume in hospitals in compliance with standard hospital and health care procedures.</div>
      <div class="cell"><span class="icon" role="img" aria-label="Factory icon"></span>Large businesses (300 people and more, manufacturing, services, etc.) will resume normal business practices. Wear of masks is recommended but not mandatory.</div>
      <div class="cell"><span class="icon" role="img" aria-label="Small shop icon"></span>Small businesses (300 people and less) will operate with the same conditions as large businesses.</div>
      <div class="cell"><span class="icon" role="img" aria-label="Store icon"></span>Commercial shops can operate on a normal mode - previous to covid- 19. Wear of masks could be recommended in certain areas.</div>
      <div class="cell"><span class="icon" role="img" aria-label="Pharmacy icon"></span>Pharmacies can operate at a normal state.</div>
      <div class="cell"><span class="icon" role="img" aria-label="Religious building icon"></span>Religious sites can operate normally. Wear of masks should be elective.</div>
      <div class="cell"><span class="icon" role="img" aria-label="Hotel icon"></span>Hotels &amp; tourism (museums, etc.) can operate at 100% capacity including all common areas</div>
      <div class="cell"><span class="icon" role="img" aria-label="Cafe icon"></span>Coffee &amp; restaurants can resume normal operations. Clients may wear masks for personal protection if they wish to.</div>
      <div class="cell"><span class="icon icon--alt" role="img" aria-label="School icon"></span>Schools can resume operations. Re-arranging school seating should continue until a vaccine is found.</div>
      <div class="cell"><span class="icon icon--alt" role="img" aria-label="Venue icon"></span>Large scale events (cinema, theaters, sport, business conferences, etc.) could resume under moderate social distancing. People may elect to wear masks.</div>
      <div class="cell cell--span2"><span class="icon" role="img" aria-label="Delivery truck icon"></span>Transportation (buses, taxis, and airlines) will operate at a normal capacity. Still no air travels permitted in and out of Covid-19 known hotspots, locally or internationally. Entry to country should be relaxed and operate normally. Airports should continue to use thermo cameras to monitor passenger's temperature at landing. Airports should be equipped to test for Covid-19 if necessary. Transportation by taxi/RideLink and buses will resume on a normal mode. Wear of masks is elective.</div>
    </div>
  </section>

  <footer class="footer">
    <div class="footer-bar">
      <div class="footer-brand"><span class="mark"></span>Civic Health Office</div>
      <p class="footer-tag"><b>#STAYHOMESAFE</b><br>Don't have to go outside? Please stay at home!</p>
      <p class="footer-info"><b>FOR INFORMATION</b><br>&#9742; 8000-1234 &nbsp; www.healthinfo.example</p>
    </div>
  </footer>

</main>
</body>
</html>
```